Briloran Clear Springs needs a new business card design (we produce and sell pure bottled water)

We need a clean modern design for our new business cards, We have an existing logo which ultimately cannot be changed, however it could be slighty improved and the colours adjusted. We have this existing logo on all of our bottles, vehicles etc.

Our company slogan is "Clear from spring to glass".
Along with our relevant company information
(Address, phone, website email etc) we will only be using names and not putting position titles for flexibilty.

We are looking for a clean, minimalist modern design.

You can view our website (if need of an update also!) to see our business.

Industry/Entity Type

Business

Contact Information for Business Card

Staff Name : XXXXXX XXXXXX
Address : 9/41 Tavenor St
Halden Rise QLD 4172
Staff Mobile Number : 04XX XXX XXX
Office Phone Number : 07 3918 2457
Staff Email Address : XXXX@brilorancleargo.com.au
Website : www.brilorancleargo.com.au

Font styles to use
Sans Serif

Colors
cee9f5
33a6d7
0492cd
0455a3
3276b5
85abd2
cedeed

Requirements
Must have
• The ability to edit and change the staff members details as we will need to edit for each respective staff member (7 in total)

```html
<!DOCTYPE html>
<html lang="en">
<head>
<meta charset="utf-8">
<title>Briloran Clear Springs – Business Card</title>
<link rel="stylesheet" href="https://fonts.googleapis.com/css2?family=Open+Sans:wght@400;600;700&display=swap">
<style>
  :root {
    --backdrop: #3a3532;
    --card: #0c0c0d;
    --card-edge: #161618;
    --brand-blue: #0492cd;
    --band-blue: #33a6d7;
    --ink: #ffffff;
    --ink-soft: #e6eef4;
  }
  * { box-sizing: border-box; margin: 0; padding: 0; }
  html, body {
    width: 1200px; height: 844px; overflow: hidden;
    background: var(--backdrop);
    font-family: "Open Sans", Arial, sans-serif;
  }
  .canvas {
    position: relative; width: 1200px; height: 844px;
    display: flex; align-items: center; justify-content: center; gap: 60px;
  }
  .card {
    position: relative; width: 520px; height: 300px;
    background: linear-gradient(160deg, var(--card-edge), var(--card));
    overflow: hidden;
    box-shadow: 0 14px 30px rgba(0,0,0,0.45);
  }

  /* Contact side */
  .card--contact .band { position: absolute; left: 0; right: 0; background: var(--band-blue); }
  .card--contact .band--top { top: 8px; height: 10px; }
  .card--contact .band--bottom { bottom: 18px; height: 16px; }
  .contact {
    position: absolute; left: 150px; top: 56px; width: 320px;
    color: var(--ink);
  }
  .contact__name { font-weight: 700; font-size: 19px; line-height: 26px; margin-left: 20px; margin-bottom: 8px; }
  .contact__line {
    display: flex; align-items: center; gap: 10px;
    font-size: 14px; line-height: 19px; color: var(--ink-soft);
  }
  .contact__line--phone { margin-left: 56px; }
  .contact__line--gap { margin-top: 14px; }
  .contact__line svg { width: 12px; height: 12px; flex: none; fill: var(--brand-blue); }
  .contact__address { margin-top: 18px; font-size: 14px; line-height: 19px; color: var(--ink-soft); }

  /* Brand side */
  .tab { position: absolute; width: 14px; height: 38px; background: var(--band-blue); }
  .tab--left { left: 0; top: 176px; }
  .tab--right { right: 0; top: 20px; }
  .brand {
    position: absolute; left: 0; right: 0; top: 100px;
    display: flex; flex-direction: column; align-items: center;
  }
  .brand__mark { display: flex; align-items: center; gap: 10px; }
  .brand__dot { width: 18px; height: 18px; border-radius: 50%; background: var(--brand-blue); }
  .brand__name {
    font-weight: 700; font-size: 30px; line-height: 40px; color: var(--brand-blue);
    letter-spacing: 0.5px;
  }
  .brand__slogan {
    margin-top: 14px; font-size: 13px; line-height: 18px; color: var(--ink);
    text-transform: uppercase; letter-spacing: 0.5px;
  }
</style>
</head>
<body>
<main class="canvas">
  <section class="card card--contact" aria-label="Business card, contact side">
    <div class="band band--top"></div>
    <div class="contact">
      <p class="contact__name">Marcel Dunhaven</p>
      <p class="contact__line contact__line--phone">
        <svg viewBox="0 0 12 12" aria-hidden="true"><rect x="3" y="0" width="6" height="12" rx="1.2"/><rect x="4" y="1.5" width="4" height="7.5" fill="#0c0c0d"/></svg>
        0400 581 392
      </p>
      <p class="contact__line contact__line--phone">
        <svg viewBox="0 0 12 12" aria-hidden="true"><path d="M2.4 0.6 4.3 2.5 3.3 4a7 7 0 0 0 4.7 4.7l1.5-1 1.9 1.9-1.3 1.8C5 11 1 7 0.6 1.9z"/></svg>
        07 3918 2457
      </p>
      <p class="contact__line contact__line--gap">
        <svg viewBox="0 0 12 12" aria-hidden="true"><path d="M0 2h12v8H0z"/><path d="M0 2l6 4.5L12 2" fill="none" stroke="#0c0c0d" stroke-width="1"/></svg>
        info@brilorancleargo.com.au
      </p>
      <p class="contact__line contact__line--gap">
        <svg viewBox="0 0 12 12" aria-hidden="true"><circle cx="6" cy="6" r="6"/><path d="M0.5 6h11M6 0.5v11M2 3h8M2 9h8" stroke="#0c0c0d" stroke-width="0.8" fill="none"/></svg>
        www.brilorancleargo.com.au
      </p>
      <p class="contact__address">9/41 Tavenor St Halden Rise QLD 4172</p>
    </div>
    <div class="band band--bottom"></div>
  </section>

  <section class="card card--brand" aria-label="Business card, brand side">
    <div class="tab tab--left"></div>
    <div class="tab tab--right"></div>
    <div class="brand">
      <div class="brand__mark">
        <span class="brand__dot"></span>
        <span class="brand__name">Briloran Clear Springs</span>
      </div>
      <p class="brand__slogan">Clear from spring to glass</p>
    </div>
  </section>
</main>
</body>
</html>
```